Bref créative
Safety products company
Safety products for life
Professional
Dorian K Pell
President/Founder
482 Quillmere Lane
Hollin Brook, PA 16328-4471
844.39R.GUMA (397.4862)
pell@vornatek.com
www.vornatek.com
BE PREPARED
HOME
DISASTER
CHILD
SENIOR
PET
TRAVEL
LIVE SAFELY
the logo
"stacked" logo - two more will be coming with white backgrounds as soon as I receive them
4 AI LOGOS

```html
<!DOCTYPE html>
<html lang="en">
<head>
<meta charset="utf-8">
<title>Vornatek business cards</title>
<link rel="stylesheet" href="https://fonts.googleapis.com/css2?family=Michroma&family=Open+Sans:ital,wght@0,400;0,600;1,400&display=swap">
<style>
  :root {
    --sheet: #3a3a3a;
    --sheet-dark: #2c2c2c;
    --card-dark: #333333;
    --card-dark-deep: #1e1e1e;
    --card-light: #ffffff;
    --red: #c8321f;
    --red-deep: #7e1a10;
    --red-light: #e0553c;
    --grey-text: #a9a9a9;
    --grey-dark-text: #555555;
    --label: #f2f2f2;
  }
  * { box-sizing: border-box; margin: 0; padding: 0; }
  html, body { width: 1200px; height: 838px; overflow: hidden; }
  body {
    background: radial-gradient(circle at 50% 40%, var(--sheet), var(--sheet-dark));
    font-family: "Open Sans", sans-serif;
    position: relative;
  }
  .card {
    position: absolute;
    width: 548px;
    height: 310px;
    border-radius: 12px;
    overflow: hidden;
    box-shadow: 0 3px 10px rgba(0,0,0,.5);
  }
  .card--dark { background: linear-gradient(180deg, var(--card-dark) 50%, var(--card-dark-deep)); }
  .card--light { background: var(--card-light); border-radius: 22px; }
  .front-left  { left: 48px;  top: 43px; }
  .front-right { left: 614px; top: 43px; }
  .back-left   { left: 48px;  top: 420px; height: 312px; }
  .back-right  { left: 614px; top: 420px; height: 312px; }

  .top-band {
    height: 40px;
    background: linear-gradient(180deg, var(--red-light), var(--red) 40%, var(--red-deep) 80%, rgba(126,26,16,0));
  }
  .card--light .top-band {
    height: 26px;
    background: linear-gradient(180deg, var(--red-light), var(--red) 50%, var(--red-deep));
  }

  .brand {
    position: absolute;
    left: 30px; top: 100px;
    display: flex; align-items: center; gap: 12px;
  }
  .brand-dot { width: 30px; height: 30px; border-radius: 50%; background: var(--red); }
  .brand-name {
    font-family: "Michroma", sans-serif;
    font-size: 29px;
    letter-spacing: 1px;
    color: #cfcfcf;
  }
  .card--light .brand-name { color: #6a6a6a; }

  .contacts {
    position: absolute;
    left: 30px; top: 206px;
    list-style: none;
    font-size: 8.5px;
    line-height: 11.5px;
    color: var(--grey-text);
  }
  .card--light .contacts { color: var(--grey-dark-text); }
  .contacts li { display: flex; align-items: center; gap: 6px; }
  .contacts svg { width: 7px; height: 7px; flex: none; }

  .person {
    position: absolute;
    right: 112px; top: 232px;
    text-align: right;
    line-height: 17px;
  }
  .card--light .person { right: 100px; }
  .person-name { font-style: italic; color: var(--red); font-size: 14px; }
  .person-role { color: var(--grey-text); font-size: 11.5px; }
  .card--light .person-role { color: var(--grey-dark-text); }

  .back-mark {
    position: absolute;
    left: 230px; top: 84px;
    width: 84px; height: 84px;
    background: linear-gradient(160deg, var(--red-light), var(--red-deep));
  }
  .back-right .back-mark { left: 206px; }
  .categories {
    position: absolute;
    left: 0; right: 0; top: 186px;
    text-align: center;
    font-size: 13px;
    line-height: 29px;
    color: #8a8a8a;
  }
  .back-right .categories { color: #3f3f3f; }

  .label {
    position: absolute;
    width: 548px;
    text-align: center;
    font-family: "Michroma", sans-serif;
    font-size: 18px;
    letter-spacing: 2px;
    color: var(--label);
  }
  .label-fl { left: 48px;  top: 366px; }
  .label-fr { left: 614px; top: 366px; }
  .label-bl { left: 48px;  top: 770px; }
  .label-br { left: 614px; top: 770px; }
</style>
</head>
<body>

  <section class="card card--dark front-left">
    <div class="top-band"></div>
    <div class="brand"><span class="brand-dot"></span><span class="brand-name">VORNATEK</span></div>
    <ul class="contacts">
      <li><svg viewBox="0 0 8 8"><circle cx="4" cy="4" r="3" fill="#c8321f"/></svg>844.39R.GUMA (397.4862)</li>
      <li><svg viewBox="0 0 8 8"><circle cx="4" cy="4" r="3" fill="#c8321f"/></svg>844-397-4862</li>
      <li><svg viewBox="0 0 8 8"><circle cx="4" cy="4" r="3" fill="#c8321f"/></svg>814-552-0376</li>
      <li><svg viewBox="0 0 8 8"><circle cx="4" cy="4" r="3" fill="#c8321f"/></svg>814-663-1908</li>
      <li><svg viewBox="0 0 8 8"><rect x="0.5" y="1.5" width="7" height="5" fill="none" stroke="#c8321f"/><path d="M0.5 1.5 L4 4.5 L7.5 1.5" fill="none" stroke="#c8321f"/></svg>pell@vornatek.com</li>
      <li><svg viewBox="0 0 8 8"><circle cx="4" cy="4" r="3.3" fill="none" stroke="#c8321f"/></svg>www.vornatek.com</li>
      <li><svg viewBox="0 0 8 8"><path d="M4 0.5 A2.6 2.6 0 0 1 6.6 3 C6.6 5 4 7.5 4 7.5 C4 7.5 1.4 5 1.4 3 A2.6 2.6 0 0 1 4 0.5Z" fill="#c8321f"/></svg>482 Quillmere Lane Hollin Brook, PA 16328-4471</li>
    </ul>
    <div class="person">
      <p class="person-name">Dorian K Pell</p>
      <p class="person-role">President | Founder</p>
    </div>
  </section>

  <section class="card card--light front-right">
    <div class="top-band"></div>
    <div class="brand"><span class="brand-dot"></span><span class="brand-name">VORNATEK</span></div>
    <ul class="contacts">
      <li><svg viewBox="0 0 8 8"><circle cx="4" cy="4" r="3" fill="#c8321f"/></svg>844.39R.GUMA (397.4862)</li>
      <li><svg viewBox="0 0 8 8"><circle cx="4" cy="4" r="3" fill="#c8321f"/></svg>844-397-4862</li>
      <li><svg viewBox="0 0 8 8"><circle cx="4" cy="4" r="3" fill="#c8321f"/></svg>814-552-0376</li>
      <li><svg viewBox="0 0 8 8"><circle cx="4" cy="4" r="3" fill="#c8321f"/></svg>814-663-1908</li>
      <li><svg viewBox="0 0 8 8"><rect x="0.5" y="1.5" width="7" height="5" fill="none" stroke="#c8321f"/><path d="M0.5 1.5 L4 4.5 L7.5 1.5" fill="none" stroke="#c8321f"/></svg>pell@vornatek.com</li>
      <li><svg viewBox="0 0 8 8"><circle cx="4" cy="4" r="3.3" fill="none" stroke="#c8321f"/></svg>www.vornatek.com</li>
      <li><svg viewBox="0 0 8 8"><path d="M4 0.5 A2.6 2.6 0 0 1 6.6 3 C6.6 5 4 7.5 4 7.5 C4 7.5 1.4 5 1.4 3 A2.6 2.6 0 0 1 4 0.5Z" fill="#c8321f"/></svg>482 Quillmere Lane Hollin Brook, PA 16328-4471</li>
    </ul>
    <div class="person">
      <p class="person-name">Dorian K Pell</p>
      <p class="person-role">President | Founder</p>
    </div>
  </section>

  <p class="label label-fl">BUSINESS CARD FRONT</p>
  <p class="label label-fr">BUSINESS CARD FRONT</p>

  <section class="card card--dark back-left">
    <div class="back-mark"></div>
    <p class="categories">Get Ready | House | Storm | Kids | Elders | Pets<br>Trips | Stay Secure</p>
  </section>

  <section class="card card--light back-right">
    <div class="back-mark"></div>
    <p class="categories">Get Ready | House | Storm | Kids | Elders | Pets<br>Trips | Stay Secure</p>
  </section>

  <p class="label label-bl">BUSINESS CARD BACK</p>
  <p class="label label-br">BUSINESS CARD BACK</p>

</body>
</html>
```